VELORA Brisbane Tiling Service

My name is Milos Brendt i need a business card for a new company. We are wall and floor tilers based in Brisbane, our company is Velorix Brisbane Tiling Service.
We would like a logo from our website used on our cards. Our website is www.velorix.com.au

I would like my Chatterbook and Postwave accounts on my card.

Industry/Entity Type

Business

Colors
0692cd
3176b5
33a6d7
85cae6

```html
<!DOCTYPE html>
<html lang="en">
<head>
<meta charset="utf-8">
<title>Velorix Business Card</title>
<link rel="stylesheet" href="https://fonts.googleapis.com/css2?family=Lato:wght@400;700;900&display=swap">
<style>
  :root {
    --bg: #2b2b2b;
    --card: #f4f4f4;
    --tile-light: #fafafa;
    --tile-mid: #e2e2e2;
    --blue: #0692cd;
    --blue-deep: #3176b5;
    --blue-mid: #33a6d7;
    --blue-soft: #85cae6;
    --ink: #333333;
    --grey: #555555;
    --band-grey: #6d6d6d;
  }
  * { margin: 0; padding: 0; box-sizing: border-box; }
  html, body { width: 1200px; height: 997px; overflow: hidden; }
  body {
    background: var(--bg);
    font-family: "Lato", sans-serif;
    position: relative;
  }
  .card {
    position: absolute;
    left: 280px;
    width: 640px;
    height: 366px;
    background: var(--card);
    overflow: hidden;
    box-shadow: 0 10px 30px rgba(0,0,0,.5);
  }
  .card--front { top: 90px; }
  .card--back { top: 530px; }
  .tile-field {
    position: absolute; inset: 0;
    background: radial-gradient(ellipse at 50% 40%, var(--tile-light) 0%, var(--tile-mid) 100%);
  }
  .edge-band { position: absolute; left: 0; bottom: 0; width: 640px; height: 40px; }

  .brand { position: absolute; display: flex; align-items: center; gap: 12px; }
  .brand__mark { background: var(--blue); flex: none; }
  .brand__text { display: flex; flex-direction: column; }
  .brand__name { color: var(--blue); font-weight: 400; line-height: .9; }
  .brand__tag { color: var(--grey); font-weight: 400; }

  .card--front .brand { left: 150px; top: 110px; }
  .card--front .brand__mark { width: 92px; height: 92px; }
  .card--front .brand__name { font-size: 66px; letter-spacing: -1px; }
  .card--front .brand__tag { font-size: 27px; margin-top: 2px; }
  .website {
    position: absolute; left: 0; right: 0; top: 262px;
    text-align: center; font-weight: 700; font-size: 17px;
    letter-spacing: 5px; color: var(--ink);
  }

  .card--back .brand { right: 40px; top: 40px; gap: 8px; }
  .card--back .brand__mark { width: 56px; height: 56px; }
  .card--back .brand__name { font-size: 40px; }
  .card--back .brand__tag { font-size: 16px; }

  .person { position: absolute; left: 85px; top: 70px; }
  .person__name { color: var(--blue-deep); font-weight: 900; font-size: 24px; }
  .person__role { color: var(--ink); font-size: 15px; margin-left: 16px; margin-top: 2px; }

  .estimate { position: absolute; right: 50px; top: 145px; text-align: center; }
  .estimate__label {
    display: inline-block; background: var(--blue-deep); color: #fff;
    font-weight: 900; font-size: 15px; padding: 4px 12px; border-radius: 5px;
  }
  .estimate__phone { color: var(--blue-deep); font-weight: 900; font-size: 32px; line-height: 1.1; }

  .contact-tab {
    position: absolute; left: 0; top: 200px; width: 46px; height: 138px;
    background: var(--blue); border-radius: 0 10px 10px 0;
  }
  .contact-list {
    position: absolute; left: 70px; top: 204px; list-style: none;
    color: var(--ink); font-size: 15px; line-height: 33px;
  }
</style>
</head>
<body>

<section class="card card--front" aria-label="Card front">
  <div class="tile-field" role="img" aria-label="Soft grey tile checker pattern"></div>
  <div class="brand">
    <div class="brand__mark"></div>
    <div class="brand__text">
      <span class="brand__name">velorix</span>
      <span class="brand__tag">brisbane tiling service</span>
    </div>
  </div>
  <p class="website">www.velorix.com.au</p>
  <svg class="edge-band" viewBox="0 0 640 40" aria-hidden="true">
    <rect x="0" y="22" width="640" height="18" fill="var(--band-grey)"/>
    <path d="M400 40 C410 12 420 8 450 8 L640 8 L640 40 Z" fill="#fff"/>
    <path d="M408 40 C418 16 428 14 455 14 L640 14 L640 40 Z" fill="var(--blue)"/>
  </svg>
</section>

<section class="card card--back" aria-label="Card back">
  <div class="tile-field" role="img" aria-label="Soft grey tile checker pattern"></div>
  <div class="brand">
    <div class="brand__mark"></div>
    <div class="brand__text">
      <span class="brand__name">velorix</span>
      <span class="brand__tag">brisbane tiling service</span>
    </div>
  </div>
  <div class="person">
    <p class="person__name">Milos Brendt</p>
    <p class="person__role">Owner / Founder</p>
  </div>
  <div class="estimate">
    <span class="estimate__label">CALL FOR A FREE ESTIMATE</span>
    <p class="estimate__phone">0412 963 270</p>
  </div>
  <div class="contact-tab">
    <svg width="46" height="138" viewBox="0 0 46 138" aria-hidden="true">
      <rect x="16" y="10" width="13" height="20" rx="2" fill="none" stroke="#fff" stroke-width="2"/>
      <rect x="13" y="45" width="19" height="13" fill="none" stroke="#fff" stroke-width="2"/>
      <path d="M13 45 L22.5 53 L32 45" fill="none" stroke="#fff" stroke-width="2"/>
      <circle cx="23" cy="85" r="6" fill="#fff"/>
      <circle cx="23" cy="116" r="6" fill="#fff"/>
    </svg>
  </div>
  <ul class="contact-list">
    <li>07 3182 4957</li>
    <li>info@velorix.com.au</li>
    <li>postwave.com/Infovelorix</li>
    <li>chatterbook.com/Velorix-Brisbane</li>
  </ul>
  <svg class="edge-band" viewBox="0 0 640 40" aria-hidden="true">
    <rect x="0" y="22" width="640" height="18" fill="var(--band-grey)"/>
    <path d="M400 40 C410 12 420 8 450 8 L640 8 L640 40 Z" fill="#fff"/>
    <path d="M408 40 C418 16 428 14 455 14 L640 14 L640 40 Z" fill="var(--blue)"/>
  </svg>
</section>

</body>
</html>
```